Desktop and Networking Support Course 9.17.25

Important the ad should not be very busy with the text taking up the major part of the ad .. please do not make the text so big that it takes up most of the ad..
Flyer Design Brief for Graphic Artist
also i am looking for something unique or creative that it will stand out .
Size & Layout:
Full Page with Bleed: 8” x 10.75” + 0.25” bleed on all sides.
Footer Space: Leave a 1-inch margin at the bottom for footer content (e.g., contact info, logo, or call-to-action).
Target Audience:
College-age students (around 24 years old)
Located in the USA
Interested in creative, professional, and career-building opportunities
Purpose:
To attract students to enroll in a college program
Flyer should be eye-catching, unique, and creative
Text must be clear and readable,
Design Style:
Use vector art, typography, or photography — your choice
If using photography, feature a white young professional USA citizen:
Wearing a white collared shirt
not with long hair
Creative Direction:
The flyer should stand out visually — something people would want to look at and keep
Showcase creativity and professionalism
Use bold colors, dynamic layout, or unexpected design elements to grab attention
Avoid clutter — keep the design balanced and clean
Text Suggestions (can be adjusted):
Footer,
please leave one inch on the bottom for the footer

```html
<!DOCTYPE html>
<html lang="en">
<head>
<meta charset="utf-8">
<title>Desktop &amp; Network Support Course Flyer</title>
<link rel="stylesheet" href="https://fonts.googleapis.com/css2?family=Montserrat:wght@400;500;600;700;800;900&family=PT+Sans&display=swap">
<style>
  :root {
    --page: #ffffff;
    --cream: #fef7ec;
    --orange: #faae1c;
    --orange-soft: #fdc667;
    --orange-bar: #fab22f;
    --orange-text: #f7931e;
    --label: #f7a541;
    --ink: #111111;
    --footer: #37414b;
    --white: #ffffff;
  }
  * { margin: 0; padding: 0; box-sizing: border-box; }
  html, body { width: 1200px; height: 1200px; overflow: hidden; background: var(--page); }
  body { position: relative; font-family: "Montserrat", sans-serif; color: var(--ink); }

  .size-label {
    position: absolute; right: 227px; top: 62px;
    font-family: "PT Sans", sans-serif; font-size: 20px; color: var(--label); line-height: 1;
  }

  .flyer {
    position: absolute; left: 230px; top: 120px; width: 747px; height: 988px;
    background: var(--cream); overflow: hidden;
  }
  .flyer-shapes { position: absolute; inset: 0; }
  .flyer > p, .flyer > h1, .flyer > h2, .flyer > ul, .flyer > div { position: absolute; }

  .title { left: 66px; top: 0; font-weight: 900; font-size: 58px; line-height: 1; letter-spacing: -1.5px; }
  .title span { position: absolute; left: 0; white-space: nowrap; }

  .tagline { left: 66px; top: 386px; font-weight: 700; font-size: 37.5px; line-height: 44px; color: var(--orange-text); white-space: nowrap; }

  .highlights-heading { left: 66px; top: 528px; font-weight: 500; font-size: 21px; line-height: 1; }
  .highlights { left: 66px; top: 0; list-style: none; }
  .highlights li { position: absolute; left: 0; white-space: nowrap; font-weight: 500; font-size: 14px; line-height: 1; padding-left: 26.5px; }
  .highlights svg { position: absolute; left: 2px; top: -3px; width: 19px; height: 19px; }

  .options { left: 66px; top: 800px; font-weight: 700; font-size: 18.3px; line-height: 27px; white-space: nowrap; }

  .feature-text { left: 468px; font-size: 19.6px; line-height: 26px; white-space: nowrap; }
  .feature-text strong { font-weight: 700; display: block; }

  .enroll { left: 66px; top: 902px; font-weight: 700; font-size: 27px; line-height: 1; color: var(--orange); }
  .contact { top: 913px; font-size: 10.4px; line-height: 1; color: var(--white); white-space: nowrap; }
</style>
</head>
<body>
  <p class="size-label">Size: 8″ x 10.75″ + 0.25″ bleed</p>

  <main class="flyer">
    <svg class="flyer-shapes" width="747" height="988" viewBox="0 0 747 988">
      <defs>
        <linearGradient id="photoTone" x1="0" y1="0" x2="1" y2="1">
          <stop offset="0" stop-color="#ffffff"/>
          <stop offset="1" stop-color="#ececec"/>
        </linearGradient>
      </defs>
      <!-- warm header field -->
      <rect class="header-field" x="0" y="0" width="600" height="344" fill="var(--orange-soft)"/>
      <!-- arc frame -->
      <circle class="photo-ring" cx="639" cy="230" r="316" fill="var(--orange)"/>
      <circle class="photo" role="img" aria-label="Photo of a smiling young professional with short hair and glasses, wearing a white collared shirt, arms crossed"
              cx="639" cy="230" r="300" fill="url(#photoTone)"/>
      <!-- title bars -->
      <rect x="-10" y="66" width="455" height="64" rx="6" fill="var(--orange-bar)" opacity="0.92"/>
      <rect x="-10" y="135" width="424" height="64" rx="6" fill="var(--orange-bar)" opacity="0.92"/>
      <rect x="-10" y="204" width="394" height="65" rx="6" fill="var(--orange-bar)" opacity="0.92"/>
      <rect x="-10" y="274" width="347" height="64" rx="6" fill="var(--orange-bar)" opacity="0.92"/>
      <!-- options band -->
      <rect x="-10" y="792" width="388" height="62" rx="5" fill="var(--orange)"/>
      <!-- feature card -->
      <rect x="387.5" y="594" width="311" height="262" rx="25" fill="var(--orange)"/>
      <circle cx="432.5" cy="643" r="21" fill="var(--white)"/>
      <circle cx="432.5" cy="722" r="21" fill="var(--white)"/>
      <circle cx="432.5" cy="801" r="21" fill="var(--white)"/>
      <!-- wifi icon -->
      <g fill="none" stroke="var(--ink)" stroke-width="3" stroke-linecap="round">
        <path d="M419 637 Q432.5 625 446 637"/>
        <path d="M423.5 642 Q432.5 634 441.5 642"/>
        <path d="M428 647 Q432.5 643 437 647"/>
      </g>
      <circle cx="432.5" cy="652" r="2.5" fill="var(--ink)"/>
      <!-- envelope icon -->
      <rect x="419" y="713" width="27" height="19" rx="1.5" fill="var(--ink)"/>
      <path d="M420.5 714.5 L432.5 724 L444.5 714.5 M420.5 730.5 L429 722 M444.5 730.5 L436 722" stroke="var(--white)" stroke-width="1.6" fill="none"/>
      <!-- thumbs up icon -->
      <g fill="none" stroke="var(--ink)" stroke-width="2" stroke-linejoin="round">
        <rect x="420" y="799" width="6" height="13" rx="1"/>
        <path d="M426 799 L431 792 Q432 786 435 787 Q437 788 436 794 L435 797 L443 797 Q446 798 445 801 L443 810 Q442 812 439 812 L426 812"/>
      </g>
      <!-- footer -->
      <rect class="footer" x="0" y="878" width="747" height="110" fill="var(--footer)"/>
      <line x1="254" y1="900" x2="254" y2="940" stroke="var(--orange)" stroke-width="1"/>
      <circle cx="300" cy="917" r="8" fill="var(--orange)"/>
      <path d="M296.5 912.5 Q296 918 302 921.5 L304 919.5 L302 917.5 L300.5 918.5 Q298.5 917 298.5 915 L299.5 914 L297.8 911.8 Z" fill="var(--footer)"/>
      <circle cx="419" cy="917" r="8" fill="var(--orange)"/>
      <rect x="414.5" y="913.5" width="9" height="7" fill="var(--footer)"/>
      <path d="M414.5 913.5 L419 917.5 L423.5 913.5" stroke="var(--orange)" stroke-width="1" fill="none"/>
      <circle cx="579" cy="917" r="8" fill="var(--orange)"/>
      <g fill="none" stroke="var(--footer)" stroke-width="1">
        <circle cx="579" cy="917" r="5"/>
        <ellipse cx="579" cy="917" rx="2.2" ry="5"/>
        <line x1="574" y1="917" x2="584" y2="917"/>
      </g>
    </svg>

    <h1 class="title">
      <span style="top:71px">DESKTOP &amp;</span>
      <span style="top:139px">NETWORK</span>
      <span style="top:208px">SUPPORT</span>
      <span style="top:277px">COURSE</span>
    </h1>

    <p class="tagline">Your Career Is<br>Just a Click Away</p>

    <h2 class="highlights-heading">Highlights &amp; billets</h2>
    <ul class="highlights">
      <li style="top:573px"><svg viewBox="0 0 20 20"><path d="M17 9.5 A7.5 7.5 0 1 1 12.5 3" fill="none" stroke="var(--orange)" stroke-width="2" stroke-linecap="round"/><path d="M6 9.5 L9.5 13 L17.5 4" fill="none" stroke="var(--orange)" stroke-width="2" stroke-linecap="round" stroke-linejoin="round"/></svg>Master Desktop Operating Systems</li>
      <li style="top:625px"><svg viewBox="0 0 20 20"><path d="M17 9.5 A7.5 7.5 0 1 1 12.5 3" fill="none" stroke="var(--orange)" stroke-width="2" stroke-linecap="round"/><path d="M6 9.5 L9.5 13 L17.5 4" fill="none" stroke="var(--orange)" stroke-width="2" stroke-linecap="round" stroke-linejoin="round"/></svg>90% Employment Rate – Class of 2024</li>
      <li style="top:677px"><svg viewBox="0 0 20 20"><path d="M17 9.5 A7.5 7.5 0 1 1 12.5 3" fill="none" stroke="var(--orange)" stroke-width="2" stroke-linecap="round"/><path d="M6 9.5 L9.5 13 L17.5 4" fill="none" stroke="var(--orange)" stroke-width="2" stroke-linecap="round" stroke-linejoin="round"/></svg>Prepare for 3 of the Top 10 Tech Jobs</li>
      <li style="top:728px"><svg viewBox="0 0 20 20"><path d="M17 9.5 A7.5 7.5 0 1 1 12.5 3" fill="none" stroke="var(--orange)" stroke-width="2" stroke-linecap="round"/><path d="M6 9.5 L9.5 13 L17.5 4" fill="none" stroke="var(--orange)" stroke-width="2" stroke-linecap="round" stroke-linejoin="round"/></svg>National College Rankings 2025</li>
    </ul>

    <p class="options">In-Person and Remote Options<br>Partial Scholarships Offered</p>

    <p class="feature-text" style="top:621px"><strong>Hands-On Desktop &amp;</strong>Network Training</p>
    <p class="feature-text" style="top:701px;left:463px"><strong>Real-World</strong>Troubleshooting Skills</p>
    <p class="feature-text" style="top:780px"><strong>Ready for</strong>IT Jobs</p>

    <p class="enroll">Enroll Today</p>
    <p class="contact" style="left:315px">555-014-2290</p>
    <p class="contact" style="left:434px">info@techpath.com</p>
    <p class="contact" style="left:594px">www.techpath.com</p>
  </main>
</body>
</html>
```